Velk Partners Building Business Cards

We need a business card that reflects our business as "Solar Experts" in San Diego. Browse our website www.velkpartners.example our License needs to be displayed as "CSLB# 3867140" our phone number is (619) 555-0187

Save thousands on your electric bills and increase the value of your home while helping to protect the environment. Our solar installation experts will help you design the system that's right for you, using only the highest quality equipment that will look great and give you ideal performance. Our goal is to make you energy independent, and get your electric bill to 0.

Paul Osterby
(619) 555-0187
paul@velkpartners.example

Target Market(s)

Home owners in san diego looking for solar

Industry/Entity Type

Solar Energy

Contact Information for Business Card

Paul Osterby
(619) 555-0187
paul@velkpartners.example

Font styles to use
Other font styles liked:
• Use our logo font

Requirements
Must have
• License needs to be displayed as "CSLB# 3867140" our phone number is (619) 555-0187
Nice to have
• Real images of rooftop home solar in san diego
Should not have
• our business address

```html
<!DOCTYPE html>
<html lang="en">
<head>
<meta charset="utf-8">
<title>Velk Partners Building – Business Cards</title>
<link href="https://fonts.googleapis.com/css2?family=Roboto:wght@400;500;700&display=swap" rel="stylesheet">
<style>
  :root {
    --bg: #b3b0b0;
    --card-blue: #2d4f9c;
    --card-blue-deep: #244186;
    --gold: #eda812;
    --white: #ffffff;
    --icon-navy: #23396f;
  }
  * { box-sizing: border-box; margin: 0; padding: 0; }
  html, body { width: 1200px; height: 1200px; overflow: hidden; }
  body {
    background: var(--bg);
    font-family: "Roboto", Arial, sans-serif;
    color: var(--white);
    position: relative;
  }
  .card {
    position: absolute;
    width: 712px;
    height: 418px;
    border-radius: 22px;
    overflow: hidden;
    background: var(--card-blue);
  }
  .card--front { left: 238px; top: 118px; }
  .card--back  { left: 231px; top: 644px; }
  .card__photo {
    position: absolute; inset: 0;
    background: linear-gradient(150deg, #35589f 0%, var(--card-blue) 45%, var(--card-blue-deep) 100%);
  }
  .brand-name {
    position: absolute;
    font-weight: 700;
    color: var(--white);
    white-space: nowrap;
    letter-spacing: -0.5px;
  }
  .card--front .brand-name {
    left: 0; right: 0; top: 62px;
    text-align: center;
    font-size: 50px;
  }
  .card--back .brand-name {
    right: 40px; top: 42px;
    font-size: 33px;
  }
  .process-title {
    position: absolute;
    left: 0; right: 0; top: 206px;
    display: flex; justify-content: center; align-items: center; gap: 26px;
    font-size: 22px; font-weight: 400; letter-spacing: 4px;
  }
  .process-title::before, .process-title::after {
    content: ""; width: 54px; height: 3px; background: var(--gold);
  }
  .process-steps {
    position: absolute; left: 92px; top: 252px;
    width: 529px; height: 120px;
  }
  .process-steps__line {
    position: absolute; left: 39px; right: 39px; top: 37px;
    border-top: 2px dotted var(--white);
  }
  .step {
    position: absolute; top: 0; width: 78px;
    display: flex; flex-direction: column; align-items: center;
  }
  .step:nth-of-type(1) { left: 0; }
  .step:nth-of-type(2) { left: 150px; }
  .step:nth-of-type(3) { left: 300px; }
  .step:nth-of-type(4) { left: 451px; }
  .step__icon {
    width: 78px; height: 78px; background: var(--gold);
    display: flex; align-items: center; justify-content: center;
  }
  .step__label {
    margin-top: 6px; width: 140px; text-align: center;
    font-size: 13.5px; line-height: 15px;
  }
  .contact {
    position: absolute; left: 41px; top: 226px;
  }
  .contact__name { font-size: 25px; font-weight: 700; letter-spacing: -0.3px; }
  .contact__role { font-size: 17px; margin-top: 4px; }
  .contact__list { list-style: none; margin-top: 30px; font-size: 18px; line-height: 25px; }
  .contact__list li { display: flex; align-items: center; gap: 14px; }
  .contact__list svg { width: 21px; height: 16px; }
</style>
</head>
<body>

<section class="card card--front">
  <div class="card__photo" role="img" aria-label="Blue-tinted photograph of rooftop solar panels"></div>
  <div class="brand-name">Velk Partners Building</div>
  <div class="process-title">OUR PROCESS</div>
  <div class="process-steps">
    <div class="process-steps__line"></div>
    <div class="step">
      <div class="step__icon">
        <svg width="40" height="40" viewBox="0 0 40 40" fill="none" stroke="var(--icon-navy)" stroke-width="3">
          <circle cx="16" cy="16" r="10"/>
          <line x1="23" y1="23" x2="34" y2="34" stroke-width="5" stroke-linecap="round"/>
        </svg>
      </div>
      <div class="step__label">Site<br>Evaluation</div>
    </div>
    <div class="step">
      <div class="step__icon">
        <svg width="40" height="40" viewBox="0 0 40 40" fill="none" stroke="var(--icon-navy)" stroke-width="2.5" stroke-linejoin="round">
          <path d="M8 6 L33 31 L35 36 L30 34 L5 9 Z"/>
          <line x1="11" y1="12" x2="14" y2="9"/>
        </svg>
      </div>
      <div class="step__label">Design &amp;<br>Permitting</div>
    </div>
    <div class="step">
      <div class="step__icon">
        <svg width="44" height="40" viewBox="0 0 44 40">
          <rect x="8" y="6" width="32" height="22" rx="3" fill="var(--icon-navy)" transform="rotate(-10 24 17)"/>
          <rect x="4" y="13" width="34" height="22" rx="3" fill="var(--icon-navy)" stroke="var(--gold)" stroke-width="1.5"/>
          <rect x="4" y="18" width="34" height="4" fill="var(--gold)"/>
          <rect x="9" y="27" width="9" height="3" fill="var(--gold)"/>
        </svg>
      </div>
      <div class="step__label">Purchase of<br>Materials</div>
    </div>
    <div class="step">
      <div class="step__icon">
        <svg width="44" height="44" viewBox="0 0 44 44" fill="none" stroke="var(--icon-navy)" stroke-linecap="round">
          <line x1="8" y1="8" x2="30" y2="30" stroke-width="3"/>
          <line x1="29" y1="29" x2="37" y2="37" stroke-width="6"/>
          <path d="M36 8 a6 6 0 1 0 0 0.1 M30 14 L9 35" stroke-width="4"/>
          <circle cx="33" cy="11" r="5" stroke-width="3"/>
        </svg>
      </div>
      <div class="step__label">Installation &amp;<br>Commissioning</div>
    </div>
  </div>
</section>

<section class="card card--back">
  <div class="card__photo" role="img" aria-label="Blue-tinted photograph of rooftop solar panels"></div>
  <div class="brand-name">Velk Partners Building</div>
  <div class="contact">
    <div class="contact__name">Paul Osterby</div>
    <div class="contact__role">Managing Director</div>
    <ul class="contact__list">
      <li>
        <svg viewBox="0 0 21 16" fill="var(--white)"><path d="M1 5 Q10.5 -1 20 5 L17 7 L15 5 L6 5 L4 7 Z"/><rect x="4" y="8" width="13" height="7" rx="1"/></svg>
        (619) 555-0187
      </li>
      <li>
        <svg viewBox="0 0 21 16" fill="none" stroke="var(--white)" stroke-width="2"><rect x="1" y="2" width="19" height="12"/><path d="M1 2 L10.5 9 L20 2"/></svg>
        paul@velkpartners.example
      </li>
      <li>License: CSLB# 3867140</li>
    </ul>
  </div>
</section>

</body>
</html>
```